Business card design for my company.
I would like the card's background colour to be black. You can also see our web site to get an idea of our brand. https://www.tmwhomecrafting.com.au/
- Name
- Email

```html
<!DOCTYPE html>
<html lang="en">
<head>
<meta charset="utf-8">
<title>TMW Home Crafting – Business Card</title>
<link rel="stylesheet" href="https://fonts.googleapis.com/css2?family=Montserrat:wght@400;500;700&display=swap">
<style>
  :root {
    --stage: #1c1c1c;
    --card-light: #f2f2f2;
    --card-dark: #151515;
    --card-dark-soft: #2a2a2a;
    --brand-green: #0f9a48;
    --ink: #1e1e1e;
    --white: #f4f4f4;
  }
  * { margin: 0; padding: 0; box-sizing: border-box; }
  html, body { width: 1200px; height: 1059px; overflow: hidden; }
  body {
    background: var(--stage);
    font-family: "Montserrat", Arial, sans-serif;
    position: relative;
  }
  .card {
    position: absolute;
    left: 255px;
    width: 690px;
    height: 393px;
    border-radius: 18px;
    overflow: hidden;
    box-shadow: 0 14px 30px rgba(0,0,0,.55);
  }
  .card-front { top: 89px; background: var(--card-light); }
  .card-back {
    top: 546px;
    height: 396px;
    background: linear-gradient(125deg, var(--card-dark) 0%, var(--card-dark) 42%, var(--card-dark-soft) 62%, var(--card-dark) 100%);
  }
  .front-swoosh { position: absolute; inset: 0; width: 100%; height: 100%; }

  .contact-name {
    position: absolute; left: 25px; top: 44px;
    font-size: 30px; font-weight: 700; color: var(--brand-green);
    letter-spacing: .2px;
  }
  .contact-role {
    position: absolute; left: 25px; top: 82px;
    font-size: 17px; font-weight: 400; color: var(--ink); letter-spacing: .5px;
  }
  .contact-location {
    position: absolute; left: 25px; top: 177px;
    font-size: 17px; color: var(--ink); letter-spacing: .5px;
  }
  .contact-list { position: absolute; left: 25px; top: 270px; list-style: none; }
  .contact-list li {
    display: flex; align-items: center; gap: 8px;
    height: 27.5px; font-size: 17px; color: var(--ink); letter-spacing: .3px;
  }
  .contact-list svg { width: 17px; height: 17px; flex: none; }

  .brand-name {
    font-family: "Montserrat", Arial, sans-serif;
    font-weight: 700; color: var(--white);
    display: flex; align-items: center; white-space: nowrap;
  }
  .brand-mark { background: var(--brand-green); flex: none; }
  .front-brand {
    position: absolute; left: 425px; top: 180px; width: 250px;
    justify-content: center; font-size: 22px; gap: 10px;
  }
  .front-brand .brand-mark { width: 14px; height: 14px; }
  .back-brand {
    position: absolute; left: 0; right: 0; top: 170px;
    justify-content: center; font-size: 42px; gap: 18px; letter-spacing: 1px;
  }
  .back-brand .brand-mark { width: 26px; height: 26px; }
</style>
</head>
<body>

  <section class="card card-front" aria-label="Business card front">
    <svg class="front-swoosh" viewBox="0 0 690 393" preserveAspectRatio="none" aria-hidden="true">
      <path d="M482,0 C385,105 335,215 352,305 C360,345 380,372 402,393 L690,393 L690,0 Z" fill="var(--brand-green)"/>
      <path d="M532,0 C445,90 365,200 372,290 C376,335 405,370 440,393 L690,393 L690,0 Z" fill="var(--card-dark)"/>
      <path d="M400,120 C375,170 365,230 372,290 C378,335 400,368 430,393" fill="none" stroke="var(--brand-green)" stroke-width="4"/>
    </svg>

    <h1 class="contact-name">Liam Carver</h1>
    <p class="contact-role">General Manager</p>
    <p class="contact-location">Riverton, Tasmania, Australia</p>

    <ul class="contact-list">
      <li>
        <svg viewBox="0 0 24 24" aria-hidden="true"><path fill="var(--brand-green)" d="M3 8c0-2 4-4 9-4s9 2 9 4v2h-5V8H8v2H3zM6 11h12l2 9H4z"/></svg>
        0400 123 456
      </li>
      <li>
        <svg viewBox="0 0 24 24" aria-hidden="true"><rect x="2" y="5" width="20" height="14" fill="var(--brand-green)"/><path d="M2 5l10 8 10-8" fill="none" stroke="var(--card-light)" stroke-width="1.8"/></svg>
        info@tmwhomecrafting.com.au
      </li>
      <li>
        <svg viewBox="0 0 24 24" aria-hidden="true"><circle cx="12" cy="12" r="10" fill="var(--brand-green)"/><path d="M7 6c3 1 4 4 2 6s-1 5 1 7M15 4c-1 3 1 4 3 5s2 4 0 6" fill="none" stroke="var(--card-light)" stroke-width="2"/></svg>
        www.tmwhomecrafting.com.au
      </li>
    </ul>

    <div class="brand-name front-brand"><span class="brand-mark"></span>TMW Home Crafting</div>
  </section>

  <section class="card card-back" aria-label="Business card back">
    <div class="brand-name back-brand"><span class="brand-mark"></span>TMW Home Crafting</div>
  </section>

</body>
</html>
```